Fizz's Shed & Grill Burger Restaurant Website - HomePage Only PSD

I need a website design for a restaurant called "Fizz's Shed and Grill" featuring burgers, wings, beer, live music, trivia, and more. I have several images of the restaurant and they already have their logo files created (see attached). I want some type of wood background and integrate the silver tin. This needs to be a modern, hip and fun type design. Design must incorporate these attached graphics.

UPDATE - just added a few more images of things I really like to be incorporated into my designs.
Updates

Industry/Entity Type

Burger Restaurant

Number of Pages Required

1 page

Font styles to use
Sans Serif

Requirements
Must have
• Restaurant/Bar theme with integration of existing logo and the red wood look.
Nice to have
• - Modern Fun appearance
• - Use Pelko Fonts

```html
<!DOCTYPE html>
<html lang="en">
<head>
<meta charset="utf-8">
<title>Fizz's Shed &amp; Grill</title>
<link rel="stylesheet" href="https://fonts.googleapis.com/css2?family=Short+Stack&family=Raleway:wght@400;600;700&display=swap">
<style>
:root{
  --red:#d4141c;
  --green:#7aa81e;
  --orange:#f08a24;
  --ink:#222;
  --muted:#8a8a8a;
  --white:#fff;
  --navy:#262a35;
  --dark-box:#2a2a2a;
  --silver-a:#cfd0d2;
  --silver-b:#e9eaeb;
  --silver-c:#b9babd;
}
*{box-sizing:border-box;margin:0;padding:0}
html,body{width:1200px;height:3285px;overflow:hidden;background:var(--white)}
body{font-family:"Raleway",sans-serif;color:var(--ink)}
.page{position:relative;width:1200px;height:3285px;overflow:hidden}
.abs{position:absolute}
.hand{font-family:"Short Stack",cursive}
.silver{background:linear-gradient(180deg,var(--silver-b) 0%,var(--silver-a) 45%,var(--silver-b) 70%,var(--silver-c) 100%)}

/* header */
.site-header{left:0;top:0;width:1200px;height:153px;background:var(--white);border-bottom:3px solid var(--green)}
.nav-link{position:absolute;top:64px;font-size:15px;color:#333;transform:translateX(-50%)}
.nav-home{position:absolute;left:147px;top:76px;width:80px;height:80px;margin:-40px 0 0 -40px;border:2px solid var(--green);border-radius:50%;display:flex;align-items:center;justify-content:center;color:var(--green);font-size:15px}
.nav-home::before{content:"";position:absolute;inset:5px;border:1px solid #ccc;border-radius:50%}
.brand-mark{position:absolute;width:120px;height:120px;border:3px solid #222;border-radius:50%;display:flex;align-items:center;justify-content:center;text-align:center;font-family:"Short Stack",cursive;font-size:15px;line-height:1.25;color:#222;background:var(--white)}
.site-header .brand-mark{left:542px;top:16px}

/* hero */
.hero{left:0;top:156px;width:1200px;height:549px;background:linear-gradient(100deg,#6f8aa3 0%,#a7866a 35%,#7a6250 60%,#9a8b7e 85%,#cfc6bb 100%)}
.hero-copy{left:652px;top:255px;color:var(--white)}
.hero-copy .we{font-size:26px}
.hero-copy h1{font-family:"Short Stack",cursive;font-weight:400;font-size:44px;color:var(--red);line-height:1.1}
.hero-copy p{font-family:"Short Stack",cursive;font-size:22px}
.slide-btn{top:495px;width:26px;height:30px;background:#f2f2f2;border:1px solid #999}
.slide-btn svg{display:block;margin:9px auto}

/* features */
.features{left:0;top:705px;width:1200px;height:407px}
.feature-divider{top:30px;width:2px;height:350px;background:rgba(255,255,255,.7);box-shadow:1px 0 0 rgba(0,0,0,.08)}
.feature{position:absolute;top:80px;width:320px;text-align:center;transform:translateX(-50%)}
.feature-icon{width:152px;height:152px;margin:0 auto;border-radius:50%;background:var(--white);border:2px solid #555;display:flex;align-items:center;justify-content:center;box-shadow:0 0 0 6px rgba(255,255,255,.6)}
.feature h3{font-family:"Short Stack",cursive;font-weight:400;font-size:28px;color:var(--red);margin-top:36px}
.feature p{font-size:15px;color:#666}
.feature a{display:block;margin-top:14px;font-size:13px;color:var(--white);text-decoration:none}
.features-next{left:1152px;top:175px}

/* about */
.about{left:0;top:1117px;width:1200px;height:547px;background:radial-gradient(circle at 70% 50%,#c9d4a5 0%,#9a8a70 40%,#5a5249 100%)}
.about-photo{left:118px;top:1185px;width:624px;height:414px;border:5px solid var(--white);background:linear-gradient(180deg,#5aa8e6 0%,#6fb5e9 35%,#9a4a2e 45%,#7f3a24 100%)}
.about-box{left:629px;top:1200px;width:516px;height:355px;background:var(--dark-box);border:2px solid #555;text-align:center;color:#bbb}
.about-box .brand-mark{position:relative;margin:35px auto 0;border-color:var(--white);color:var(--white);background:transparent;width:120px;height:120px}
.about-box p{margin:32px 40px 0;font-size:12.5px;line-height:1.85}
.about-box a{display:block;margin-top:16px;color:var(--white);font-size:13px;text-decoration:none}

/* menu */
.menu{left:0;top:1664px;width:1200px;height:916px}
.menu h2{position:absolute;top:55px;width:100%;text-align:center;font-family:"Short Stack",cursive;font-weight:400;font-size:34px;color:#222}
.menu-lead{position:absolute;top:114px;width:100%;text-align:center;font-size:14px}
.menu-note{position:absolute;top:138px;width:100%;text-align:center;font-size:13px;color:var(--orange)}
.dish{position:absolute;width:245px}
.dish-photo{width:245px;height:193px}
.dish h4{margin-top:22px;font-size:13px;font-weight:700;color:#222}
.dish p{margin-top:6px;font-size:11.5px;line-height:1.6;color:var(--muted);padding-bottom:12px;border-bottom:1px dashed #999}

/* banner */
.banner{left:0;top:2580px;width:1200px;height:322px;background:linear-gradient(90deg,#2b2622 0%,#4a3e36 45%,#3a332f 70%,#231f1d 100%)}
.banner-text{position:absolute;top:100px;width:100%;text-align:center;font-family:"Short Stack",cursive;font-size:44px;line-height:1.25;color:var(--white)}

/* footer */
.footer-top{left:0;top:2902px;width:1200px;height:230px}
.footer-title{position:absolute;top:50px;font-family:"Short Stack",cursive;font-size:17px;color:#333}
.footer-title span{color:var(--green)}
.foot-link{position:absolute;font-size:12px;color:#444}
.foot-link::before{content:"›";color:var(--green);margin-right:8px}
.news-input{left:457px;top:94px;width:296px;height:37px;background:var(--white);border:1px solid #ccc;font-size:11px;color:#999;padding:11px 10px}
.news-btn{left:457px;top:138px;width:296px;height:35px;background:var(--green);color:var(--white);font-size:12px;text-align:center;line-height:35px}
.social{width:34px;height:34px;border:2px solid var(--white);border-radius:50%;top:98px}

.footer-bottom{left:0;top:3132px;width:1200px;height:153px;background:var(--navy);color:var(--white);font-size:12px}
.hours{position:absolute;left:88px;line-height:26px;top:32px}
.hours div{display:flex;gap:6px}
.hours .dots{width:130px;border-bottom:1px dotted #bbb;height:14px}
.footer-bottom .brand-mark{left:540px;top:16px;background:transparent;border-color:var(--white);color:var(--white)}
.legal{position:absolute;right:79px;top:32px;text-align:right;line-height:26px}
.legal .name{font-family:"Short Stack",cursive;color:var(--green);font-size:14px}
.legal .terms{color:var(--red)}
.legal .terms b{color:var(--white);font-weight:400}
</style>
</head>
<body>
<div class="page">

  <header class="site-header abs">
    <div class="nav-home">Home</div>
    <span class="nav-link" style="left:285px">About</span>
    <span class="nav-link" style="left:431px">Foods</span>
    <div class="brand-mark">Fizz's<br>Shed &amp;<br>Grill</div>
    <span class="nav-link" style="left:782px">News</span>
    <span class="nav-link" style="left:920px">Store</span>
    <span class="nav-link" style="left:1069px">Contact</span>
  </header>

  <section class="hero abs" role="img" aria-label="Photo of two guests smiling while eating at a restaurant table"></section>
  <div class="hero-copy abs">
    <div class="we">We are</div>
    <h1>Fizz's Shed &amp; Grill</h1>
    <p>based in united states of america</p>
  </div>
  <div class="slide-btn abs" style="left:572px;top:650px"><svg width="8" height="10"><path d="M6 1L2 5l4 4" stroke="#333" fill="none" stroke-width="1.5"/></svg></div>
  <div class="slide-btn abs" style="left:599px;top:650px"><svg width="8" height="10"><path d="M2 1l4 4-4 4" stroke="#333" fill="none" stroke-width="1.5"/></svg></div>

  <section class="features abs silver">
    <div class="feature-divider abs" style="left:394px"></div>
    <div class="feature-divider abs" style="left:800px"></div>
    <div class="feature" style="left:191px">
      <div class="feature-icon"><svg width="80" height="80" viewBox="0 0 80 80"><circle cx="40" cy="40" r="38" fill="var(--red)"/><path d="M22 38a18 13 0 0 1 36 0z" fill="#fff"/><rect x="22" y="41" width="36" height="5" rx="2" fill="#fff"/><rect x="22" y="49" width="36" height="9" rx="3" fill="#fff"/></svg></div>
      <h3>Burgers</h3><p>Lorem ipsum dolor sit amet</p><a>View Now</a>
    </div>
    <div class="feature" style="left:607px">
      <div class="feature-icon"><svg width="80" height="80" viewBox="0 0 80 80"><circle cx="40" cy="40" r="38" fill="var(--red)"/><circle cx="40" cy="40" r="22" fill="none" stroke="#fff" stroke-width="3"/><circle cx="40" cy="40" r="6" fill="#fff"/></svg></div>
      <h3>Live Music</h3><p>Lorem ipsum dolor sit amet</p><a>View Now</a>
    </div>
    <div class="feature" style="left:1012px">
      <div class="feature-icon"><svg width="80" height="80" viewBox="0 0 80 80"><circle cx="40" cy="40" r="38" fill="var(--red)"/><rect x="24" y="26" width="26" height="34" rx="3" fill="#fff"/><path d="M50 32h6a4 4 0 0 1 4 4v10a4 4 0 0 1-4 4h-6" stroke="#fff" stroke-width="4" fill="none"/></svg></div>
      <h3>Beer</h3><p>Lorem ipsum dolor sit amet</p><a>View Now</a>
    </div>
    <svg class="features-next abs" width="20" height="40"><path d="M4 4l12 16-12 16" stroke="#fff" stroke-width="2" fill="none"/></svg>
  </section>

  <section class="about abs" role="img" aria-label="Photo of a fresh salad plate"></section>
  <div class="about-photo abs" role="img" aria-label="Photo of the restaurant's red wooden barn front with its sign"></div>
  <div class="about-box abs">
    <div class="brand-mark">Fizz's<br>Shed &amp;<br>Grill</div>
    <p>Lorem ipsum dolor sit amet, consectetur adipiscing elit. Duis vitae gravida nulla. Integer fermentum dui non commodo venenatis. Vestibulum gravida dui in imperdiet tristique. Ligula libero tincidunt enim, et finibus eros massa eu elit. Etiam venenatis tortor id purus convallis volutpat.</p>
    <a>Read More &gt;&gt;</a>
  </div>

  <section class="menu abs silver">
    <h2>All Day Menu</h2>
    <p class="menu-lead">Our meat is free range &amp; organic where possible. Breads are sourdough, baked daily</p>
    <p class="menu-note">See front counter for daily sweet selection</p>

    <div class="dish" style="left:79px;top:213px"><div class="dish-photo" role="img" aria-label="Photo of crostino pie" style="background:linear-gradient(135deg,#e9e4dc,#4a2f22)"></div><h4>Crostino Pie</h4><p>with Pepa Sol butter &amp; spreads</p></div>
    <div class="dish" style="left:344px;top:213px"><div class="dish-photo" role="img" aria-label="Photo of a burger with fries" style="background:linear-gradient(135deg,#b88a4a,#5a8a2c)"></div><h4>Pollo Burger</h4><p>with Earl Grey figs, seasonal fruit &amp; yogurt</p></div>
    <div class="dish" style="left:609px;top:213px"><div class="dish-photo" role="img" aria-label="Photo of a plated eggplant pie in a restaurant" style="background:linear-gradient(135deg,#b9a58a,#6b4a3a)"></div><h4>Eggplant Special Pie</h4><p>with poached red fruits</p></div>
    <div class="dish" style="left:874px;top:213px"><div class="dish-photo" role="img" aria-label="Photo of a taco pizza" style="background:linear-gradient(135deg,#c4501e,#3b2a1e)"></div><h4>Taco Pizza</h4><p>with Earl Grey figs, seasonal fruit &amp; yogu</p></div>

    <div class="dish" style="left:79px;top:544px"><div class="dish-photo" role="img" aria-label="Photo of grilled salmon plate" style="background:linear-gradient(135deg,#7a8a3a,#a2452a)"></div><h4>Smoked Harlow salmon plate</h4><p>with toast with house made sauce pickled fennel and roe</p></div>
    <div class="dish" style="left:344px;top:544px"><div class="dish-photo" role="img" aria-label="Photo of a steak sandwich with greens" style="background:linear-gradient(135deg,#f0ede6,#d89a4a)"></div><h4>Marrow Creek wagyu steak sandwich</h4><p>with red onion jam, radicchio, tomato, house pickles &amp; aioli</p></div>
    <div class="dish" style="left:609px;top:544px"><div class="dish-photo" role="img" aria-label="Photo of breakfast dishes on a table" style="background:linear-gradient(135deg,#3a2a1e,#c2702a)"></div><h4>Buffalo's Big Breakfast</h4><p>Pork sausage, bacon, fried eggs, roast tomato, field mushrooms</p></div>
    <div class="dish" style="left:874px;top:544px"><div class="dish-photo" role="img" aria-label="Photo of a table with bottles and poached eggs" style="background:linear-gradient(135deg,#d08a3a,#3a2418)"></div><h4>Two poached eggs on sourdough</h4><p>with smoked tomato relish, field mushroom, avocado, feta</p></div>
  </section>

  <section class="banner abs" role="img" aria-label="Dim photo of diners enjoying an evening out">
    <div class="banner-text">Fizz's Shed and Grill<br>Lorem dummy text food</div>
  </section>

  <footer class="footer-top abs silver">
    <div class="footer-title" style="left:88px">Category <span>List</span></div>
    <span class="foot-link" style="left:105px;top:100px">Home</span>
    <span class="foot-link" style="left:105px;top:131px">About</span>
    <span class="foot-link" style="left:105px;top:162px">Culture</span>
    <span class="foot-link" style="left:254px;top:100px">News</span>
    <span class="foot-link" style="left:254px;top:131px">Work</span>
    <span class="foot-link" style="left:254px;top:162px">Contact</span>

    <div class="footer-title" style="left:455px">News<span>letter</span></div>
    <div class="news-input abs">Enter Your Email Address</div>
    <div class="news-btn abs">Subscribe</div>

    <div class="footer-title" style="left:854px">Follow <span>us</span></div>
    <div class="social abs" style="left:863px"></div>
    <div class="social abs" style="left:918px"></div>
    <div class="social abs" style="left:973px"></div>
    <div class="social abs" style="left:1028px"></div>
    <div class="social abs" style="left:1084px"></div>
  </footer>

  <footer class="footer-bottom abs">
    <div class="hours">
      <div>Monday <span class="dots"></span> Friday 8.00 - 22.00</div>
      <div>Saturday <span class="dots"></span> Sunday 7.30 - 22.30</div>
      <div>Holidays <span class="dots"></span> 7.00 - 24.00</div>
    </div>
    <div class="brand-mark">Fizz's<br>Shed &amp;<br>Grill</div>
    <div class="legal">
      <div class="name">Fizz's Shed and Grill</div>
      <div>© 2016 All Rights Reserved</div>
      <div class="terms">Terms of use <b>and</b> Privacy Policy</div>
    </div>
  </footer>

</div>
</body>
</html>
```